Stationery Design Project

I need a stationary design for our company. we are based in Houston, TX and we are called Mira Vell Lending. And we are wanting to brand our MoneyMendPlus program, which includes our tax preparation and restoration, credit repair service. Although our business offers other programs, we are interested in mainly focusing on The MoneyMendPlus program. We are looking for way to brand our ourselves and I believe that a great stationery design will help in achieving this goal. Our logo design is blue and light blue. the slogan is orange.

Industry/Entity Type

Business

Requirements
Must have
• Address: 30871 Calloway Ln. B-22
Houston, TX 75419
Tel. 555-318-6207
Fax 555-294-7153
www.miravelllending.example
info@miravelllending.example
Our Slogan: Happiness, Restored!

```html
<!DOCTYPE html>
<html lang="en">
<head>
<meta charset="utf-8">
<title>MoneyMendPlus Business Card</title>
<link rel="stylesheet" href="https://fonts.googleapis.com/css2?family=Tinos&family=Questrial&display=swap">
<style>
  :root {
    --navy: #123f6b;
    --blue: #1d6fa8;
    --sky: #2a8fc8;
    --orange: #f4961e;
    --ink: #2b2b2b;
    --card: #ffffff;
    --stage: #ececec;
  }
  * { margin: 0; padding: 0; box-sizing: border-box; }
  html, body { width: 1200px; height: 724px; overflow: hidden; background: var(--stage); }
  .sheet { position: relative; width: 1200px; height: 724px; }
  .card {
    position: absolute; top: 203px; width: 555px; height: 317px;
    background: var(--card); border-radius: 22px; overflow: hidden;
    box-shadow: 0 4px 14px rgba(0,0,0,.18);
  }
  .card--front { left: 30px; }
  .card--back { left: 615px; }

  .brand-name {
    font-family: "Tinos", serif; color: var(--blue); letter-spacing: -1px;
    position: absolute; white-space: nowrap;
  }
  .card--front .brand-name { left: 34px; top: 82px; font-size: 44px; }

  .company-mark { position: absolute; right: 38px; top: 22px; width: 126px; text-align: center; }
  .company-mark__square { width: 64px; height: 64px; margin: 0 auto 8px; background: var(--navy); }
  .company-mark__name { font-family: "Tinos", serif; font-size: 14px; color: var(--navy); }

  .address {
    position: absolute; left: 40px; top: 158px; width: 228px; text-align: right;
    font-family: "Questrial", sans-serif; font-size: 15px; line-height: 20px; color: var(--ink);
  }
  .divider { position: absolute; left: 282px; top: 140px; width: 1px; height: 82px; background: #bbb; }
  .contact-list {
    position: absolute; left: 292px; top: 138px; list-style: none;
    font-family: "Questrial", sans-serif; font-size: 14.5px; line-height: 21px; color: var(--ink);
  }
  .contact-list li { display: flex; align-items: center; gap: 6px; }
  .contact-list svg { width: 12px; height: 12px; fill: var(--navy); flex: none; }

  .swoosh { position: absolute; left: 0; top: 0; width: 555px; height: 317px; }
  .slogan { font-family: "Tinos", serif; font-size: 19px; fill: #fff; }

  .card--back .brand-name { left: 50%; top: 108px; transform: translateX(-50%); font-size: 64px; }
  .back-url {
    position: absolute; left: 0; right: 0; top: 212px; text-align: center;
    font-family: "Tinos", serif; font-size: 15px; letter-spacing: 4px; color: var(--ink);
  }
</style>
</head>
<body>
<main class="sheet">
  <section class="card card--front" aria-label="Card front">
    <svg class="swoosh" viewBox="0 0 555 317" aria-hidden="true">
      <path d="M0,266 C180,292 330,246 555,228 L555,236 C330,254 180,302 0,284 Z" fill="var(--orange)"/>
      <path d="M0,294 C170,312 320,262 555,242 L555,317 L0,317 Z" fill="var(--blue)"/>
      <path d="M0,308 C170,322 330,292 555,284 L555,317 L0,317 Z" fill="var(--navy)"/>
      <text class="slogan" x="372" y="284" transform="rotate(-6 372 284)">Happiness, Restored!</text>
    </svg>

    <div class="brand-name">MoneyMendPlus</div>

    <div class="company-mark">
      <div class="company-mark__square"></div>
      <div class="company-mark__name">Mira Vell Lending</div>
    </div>

    <p class="address">30871 Calloway Ln. B-22<br>Houston<br>TX 75419</p>
    <div class="divider"></div>
    <ul class="contact-list">
      <li><svg viewBox="0 0 12 12"><path d="M3 1l2 2-1 1.5c.6 1.4 1.7 2.5 3 3L8.5 6.5l2 2-1.3 1.8C5 10 2 7 1.6 2.5z"/></svg>555-318-6207</li>
      <li><svg viewBox="0 0 12 12"><path d="M3 1h5v3H3zM1 5h10v5H9V8H3v2H1z"/></svg>555-294-7153</li>
      <li><svg viewBox="0 0 12 12"><path d="M1 3h10v7H1zM1 3l5 4 5-4" stroke="#fff" stroke-width=".8"/></svg>info@miravelllending.example</li>
      <li><svg viewBox="0 0 12 12"><circle cx="6" cy="6" r="5"/><path d="M1 6h10M6 1c-2 2.5-2 7.5 0 10M6 1c2 2.5 2 7.5 0 10" stroke="#fff" stroke-width=".7" fill="none"/></svg>www.miravelllending.example</li>
    </ul>
  </section>

  <section class="card card--back" aria-label="Card back">
    <div class="brand-name">MoneyMendPlus</div>
    <p class="back-url">www.miravelllending.example</p>
  </section>
</main>
</body>
</html>
```